KRV Business Card

Looking for a business card for my restaurant group I own. Four different concepts:

Copperfield Alehouse
Bristow Alehouse
Tanager's Stone Hearth Kitchen
Pellston Patty Company

Card doesn't need to include all the logos.

```html
<!DOCTYPE html>
<html lang="en">
<head>
<meta charset="utf-8">
<title>KRV Business Card</title>
<link href="https://fonts.googleapis.com/css2?family=Open+Sans:wght@400;600&display=swap" rel="stylesheet">
<style>
  :root {
    --page: #ebebeb;
    --card: #1c1a1b;
    --gold: #c8ae72;
    --white: #f4f4f4;
  }
  * { margin: 0; padding: 0; box-sizing: border-box; }
  html, body {
    width: 1200px; height: 800px; overflow: hidden;
    background: var(--page);
    font-family: "Open Sans", sans-serif;
  }
  .card {
    position: absolute;
    left: 314px;
    width: 573px;
    height: 331px;
    background: var(--card);
    border-radius: 22px;
    overflow: hidden;
  }
  .card--front { top: 50px; }
  .card--back { top: 418px; }

  .wordmark {
    position: absolute;
    text-align: center;
    color: var(--gold);
    font-weight: 600;
    text-transform: uppercase;
    line-height: 1;
  }
  .card--front .wordmark { left: 0; right: 0; top: 100px; }
  .wordmark__initials { display: block; font-size: 66px; letter-spacing: 6px; }
  .wordmark__name { display: block; margin-top: 18px; font-size: 22px; letter-spacing: 5px; }

  .card--back .wordmark { left: 78px; width: 200px; top: 108px; }
  .card--back .wordmark__initials { font-size: 44px; letter-spacing: 4px; }
  .card--back .wordmark__name { margin-top: 14px; font-size: 14px; letter-spacing: 3px; line-height: 1.35; }

  .divider {
    position: absolute;
    left: 286px; top: 100px;
    width: 2px; height: 123px;
    background: var(--gold);
  }
  .contact {
    position: absolute;
    left: 312px; top: 94px;
    color: var(--white);
  }
  .contact__name { color: var(--gold); font-weight: 600; font-size: 20px; line-height: 26px; }
  .contact__company { font-size: 15px; line-height: 20px; margin-top: 6px; }
  .contact__list { list-style: none; margin-top: 18px; }
  .contact__item {
    display: flex; align-items: center;
    font-size: 14.5px; line-height: 20.5px;
  }
  .contact__icon { width: 11px; height: 11px; margin-right: 9px; fill: var(--gold); }

  .base-band { position: absolute; left: 0; bottom: 0; width: 573px; height: 331px; }
</style>
</head>
<body>

<section class="card card--front" aria-label="Card front">
  <div class="wordmark">
    <span class="wordmark__initials">KRV</span>
    <span class="wordmark__name">Kestrel Ridge Ventures</span>
  </div>
</section>

<section class="card card--back" aria-label="Card back">
  <div class="wordmark">
    <span class="wordmark__initials">KRV</span>
    <span class="wordmark__name">Kestrel Ridge<br>Ventures</span>
  </div>

  <div class="divider"></div>

  <div class="contact">
    <p class="contact__name">Dana Whitlow</p>
    <p class="contact__company">Kestrel Ridge Ventures</p>
    <ul class="contact__list">
      <li class="contact__item">
        <svg class="contact__icon" viewBox="0 0 12 12"><path d="M2.5 0.5 L4.5 3 L3.3 4.4 Q4.5 7 7.6 8.7 L9 7.5 L11.5 9.5 L10 11.5 Q5 11.5 0.5 3 Z"/></svg>
        555-014-2290
      </li>
      <li class="contact__item">
        <svg class="contact__icon" viewBox="0 0 12 12"><path d="M0.5 2 H11.5 V10 H0.5 Z M1.5 3 V3.4 L6 6.6 L10.5 3.4 V3 Z" fill-rule="evenodd"/></svg>
        dana@krvrestaurants.com
      </li>
      <li class="contact__item">
        <svg class="contact__icon" viewBox="0 0 12 12"><circle cx="6" cy="6" r="5.5"/></svg>
        www.krvrestaurants.com
      </li>
    </ul>
  </div>

  <svg class="base-band" viewBox="0 0 573 331" aria-hidden="true">
    <path d="M0 280 Q 290 322 573 268 L573 331 L0 331 Z" fill="var(--gold)"/>
  </svg>
</section>

</body>
</html>
```